TALMORK

The business want a professional looking business card. We have a scetch we will add but want the extra upgrade, and would like more suggestions for variations of our business cards.

```html
<!DOCTYPE html>
<html lang="en">
<head>
<meta charset="utf-8">
<title>TALMORK – Business Card</title>
<link rel="stylesheet" href="https://fonts.googleapis.com/css2?family=Montserrat:wght@400;600&family=Cinzel:wght@600&display=swap">
<style>
  :root{
    --backdrop:#33230a;
    --gold-dark:#d39a36;
    --gold:#e9b54f;
    --gold-light:#fbcf6e;
    --gold-text:#d9a03c;
    --ink:#3f3f3f;
    --muted:#6b6b6b;
    --paper:#ffffff;
    --paper-warm:#efdcc0;
  }
  *{box-sizing:border-box;}
  html,body{margin:0;padding:0;width:1031px;height:1200px;overflow:hidden;background:var(--backdrop);}
  .card{position:absolute;left:58px;width:914px;height:564px;border-radius:30px;overflow:hidden;}
  .card-front{top:20px;background:linear-gradient(210deg,var(--paper-warm) 0%,var(--paper) 45%,var(--paper) 100%);}
  .card-back{top:614px;background:linear-gradient(110deg,var(--gold-dark) 0%,var(--gold-light) 45%,var(--gold) 100%);}

  .wave-area{position:absolute;left:0;top:0;width:130px;height:100%;
    background:linear-gradient(180deg,var(--gold) 0%,var(--gold-light) 45%,var(--gold-dark) 100%);}

  .brand-block{position:absolute;text-align:center;margin:0;}
  .brand-block-front{left:136px;top:196px;width:280px;}
  .brand-block-back{left:0;top:200px;width:100%;}
  .brand-dot{display:block;margin:0 auto;border-radius:50%;}
  .brand-dot-front{width:72px;height:72px;background:var(--gold);}
  .brand-dot-back{width:100px;height:100px;background:var(--paper);}
  .brand{font-family:"Cinzel",serif;font-weight:600;letter-spacing:4px;margin:0;line-height:1;}
  .brand-front{margin-top:60px;font-size:44px;color:var(--gold-text);}
  .brand-back{margin-top:60px;font-size:58px;color:var(--paper);}
  .since{font-family:"Montserrat",sans-serif;font-weight:400;letter-spacing:4px;margin:6px 0 0;line-height:1;}
  .since-front{font-size:21px;color:var(--muted);}
  .since-back{font-size:28px;color:rgba(255,255,255,.75);}

  .person{position:absolute;left:521px;top:150px;font-family:"Montserrat",sans-serif;}
  .person p{margin:0;font-size:26px;line-height:35px;white-space:nowrap;}
  .person-company{font-weight:600;color:var(--gold-text);}
  .person-line{font-weight:400;color:var(--ink);}
  .divider{position:absolute;left:526px;top:278px;right:0;height:2px;background:var(--gold);}
  .divider::before{content:"";position:absolute;left:-5px;top:-4px;width:10px;height:10px;border-radius:50%;background:var(--gold);}

  .contact-bar{position:absolute;left:470px;top:372px;width:34px;height:192px;border-radius:17px 17px 0 0;
    background:linear-gradient(180deg,var(--gold-dark),var(--gold-light) 70%,var(--gold));}
  .contact-bar svg{display:block;margin:10px auto 0;width:18px;height:18px;}
  .contact-bar svg + svg{margin-top:24px;}
  .contacts{position:absolute;left:521px;top:378px;margin:0;padding:0;list-style:none;
    font-family:"Montserrat",sans-serif;font-size:25px;color:var(--ink);}
  .contacts li{line-height:42px;white-space:nowrap;}
</style>
</head>
<body>
  <section class="card card-front" aria-label="Business card front">
    <div class="wave-area" role="img" aria-label="Gold and black wave decoration along the left edge"></div>

    <div class="brand-block brand-block-front">
      <span class="brand-dot brand-dot-front" aria-hidden="true"></span>
      <p class="brand brand-front">TALMORK</p>
      <p class="since since-front">SINCE 2026</p>
    </div>

    <div class="person">
      <p class="person-company">TALMORK A LUNDHEIM</p>
      <p class="person-line">CEO &amp; Founder</p>
      <p class="person-line">Ola Henrik Lundheim</p>
    </div>
    <div class="divider" aria-hidden="true"></div>

    <div class="contact-bar" aria-hidden="true">
      <svg viewBox="0 0 24 24"><path fill="#fff" d="M6.6 10.8a15 15 0 0 0 6.6 6.6l2.2-2.2a1 1 0 0 1 1-.25 11.4 11.4 0 0 0 3.6.57 1 1 0 0 1 1 1V20a1 1 0 0 1-1 1A17 17 0 0 1 3 4a1 1 0 0 1 1-1h3.5a1 1 0 0 1 1 1c0 1.25.2 2.45.57 3.57a1 1 0 0 1-.25 1z"/></svg>
      <svg viewBox="0 0 24 24"><rect x="3" y="6" width="18" height="12" fill="none" stroke="#fff" stroke-width="2"/><path d="M3 6l9 7 9-7" fill="none" stroke="#fff" stroke-width="2"/></svg>
      <svg viewBox="0 0 24 24"><circle cx="12" cy="12" r="9" fill="none" stroke="#fff" stroke-width="2"/><ellipse cx="12" cy="12" rx="4" ry="9" fill="none" stroke="#fff" stroke-width="1.6"/><path d="M3 12h18M5 7.5h14M5 16.5h14" stroke="#fff" stroke-width="1.6"/></svg>
    </div>
    <ul class="contacts">
      <li>004791234567</li>
      <li>talmork.llc@example.com</li>
      <li>www.talmork.llc</li>
    </ul>
  </section>

  <section class="card card-back" aria-label="Business card back">
    <div class="brand-block brand-block-back">
      <span class="brand-dot brand-dot-back" aria-hidden="true"></span>
      <p class="brand brand-back">TALMORK</p>
      <p class="since since-back">SINCE 2026</p>
    </div>
  </section>
</body>
</html>
```